RWT Fittings Ltd Business Cards

We need a business card with our business logo. We provide window and door installations on high-rises in west coast British Colombia, Canada.

I would like my business information and details on one side of the card, and the other side the company name with logo

Target Market(s)

General Contractors

Industry/Entity Type

Construction

Contact Information for Business Card

one side i want my company name and logo in the dark theme logo that i provided

Requirements
Must have
• Marco Peltieri, 16045518293, RWTFittings@mailbox-demo.com, 1407-5194 Linden Row Burnaby BC, V5H 2K9, Owner & Manager

```html
<!DOCTYPE html>
<html lang="en">
<head>
<meta charset="utf-8">
<title>RWT Fittings Ltd – Business Cards</title>
<link href="https://fonts.googleapis.com/css2?family=Open+Sans:wght@400;600;700&display=swap" rel="stylesheet">
<style>
  :root {
    --stage-light: #5a5a5a;
    --stage-dark: #141414;
    --card-black: #1a1a1a;
    --brand-blue: #29a9e1;
    --band-grey: #9b9b9b;
    --text-white: #f2f2f2;
  }
  * { margin: 0; padding: 0; box-sizing: border-box; }
  html, body { width: 1200px; height: 780px; overflow: hidden; }
  body {
    background: linear-gradient(135deg, var(--stage-light) 0%, #3a3a3a 45%, var(--stage-dark) 100%);
    font-family: "Open Sans", Arial, sans-serif;
    position: relative;
  }
  .card {
    position: absolute;
    top: 235px;
    width: 540px;
    height: 310px;
    background: var(--card-black);
    overflow: hidden;
    box-shadow: 0 18px 40px rgba(0,0,0,.55);
  }
  .card--details { left: 40px; }
  .card--brand { left: 620px; }

  .card__wave { position: absolute; inset: 0; width: 100%; height: 100%; }

  .brand-mark {
    display: flex;
    align-items: center;
    gap: 10px;
    color: var(--brand-blue);
    font-weight: 700;
    white-space: nowrap;
  }
  .brand-mark__square { background: var(--brand-blue); flex: none; }

  .card--details .brand-mark {
    position: absolute;
    left: 38px;
    top: 72px;
    font-size: 24px;
  }
  .card--details .brand-mark__square { width: 21px; height: 21px; }

  .card__divider {
    position: absolute;
    left: 288px;
    top: 40px;
    width: 1px;
    height: 160px;
    background: var(--brand-blue);
  }

  .contact {
    position: absolute;
    left: 304px;
    top: 46px;
    width: 226px;
    color: var(--text-white);
    font-size: 12.5px;
    line-height: 1.5;
    white-space: nowrap;
  }
  .contact__name {
    color: var(--brand-blue);
    font-weight: 700;
    font-size: 18px;
    text-transform: uppercase;
    line-height: 1.2;
  }
  .contact__role { font-size: 13.5px; margin-bottom: 6px; }
  .contact__line { display: flex; align-items: center; gap: 6px; }
  .contact__icon { width: 11px; height: 11px; flex: none; }
  .contact__address { margin-top: 4px; }

  .card--brand .brand-mark {
    position: absolute;
    left: 50%;
    top: 50%;
    transform: translate(-50%, -50%);
    font-size: 44px;
    gap: 16px;
  }
  .card--brand .brand-mark__square { width: 38px; height: 38px; }
</style>
</head>
<body>

<section class="card card--details" aria-label="Business card, contact side">
  <svg class="card__wave" viewBox="0 0 540 310" preserveAspectRatio="none" aria-hidden="true">
    <path d="M0 150 C 40 250, 150 250, 300 262 C 420 272, 500 280, 540 310 L 0 310 Z" fill="var(--band-grey)"/>
    <path d="M20 150 C 70 230, 170 236, 310 248 C 420 258, 490 270, 520 300" fill="none" stroke="var(--brand-blue)" stroke-width="4"/>
  </svg>

  <div class="brand-mark">
    <span class="brand-mark__square"></span>
    <span class="brand-mark__name">RWT Fittings Ltd</span>
  </div>

  <span class="card__divider"></span>

  <div class="contact">
    <p class="contact__name">Marco Peltieri</p>
    <p class="contact__role">Owner &amp; Manager</p>
    <p class="contact__line">
      <svg class="contact__icon" viewBox="0 0 12 12" aria-hidden="true"><path d="M3 1 L5 3.5 L4 5 Q5 7 7 8 L8.5 7 L11 9 L10 11 Q5 11 1 6 Q1 3 3 1 Z" fill="var(--brand-blue)"/></svg>
      16045518293
    </p>
    <p class="contact__line">
      <svg class="contact__icon" viewBox="0 0 12 12" aria-hidden="true"><rect x="0.5" y="2" width="11" height="8" fill="var(--brand-blue)"/><path d="M0.5 2 L6 7 L11.5 2" fill="none" stroke="var(--card-black)" stroke-width="1"/></svg>
      RWTFittings@mailbox-demo.com
    </p>
    <p class="contact__line">
      <svg class="contact__icon" viewBox="0 0 12 12" aria-hidden="true"><circle cx="6" cy="6" r="5.5" fill="var(--brand-blue)"/><path d="M0.5 6 H11.5 M6 0.5 V11.5" stroke="var(--card-black)" stroke-width="0.8"/></svg>
      www.rwtfittings-demo.com
    </p>
    <p class="contact__address">1407-5194 Linden Row<br>Burnaby BC, V5H 2K9</p>
  </div>
</section>

<section class="card card--brand" aria-label="Business card, brand side">
  <div class="brand-mark">
    <span class="brand-mark__square"></span>
    <span class="brand-mark__name">RWT Fittings Ltd</span>
  </div>
</section>

</body>
</html>
```